Emergency Management Consulting Needs a Website

Need to develop a website for an Emergency Management Consulting business. This website needs to be user friendly and resemble disaster preparedness, response, recovery, and mitigation. It must allow for me to make changes to it myself by adding pages, content and pictures. Looking for an advanced page to the website that allows monitoring of social media sites, hashtags, and keywords. Must have pictures of disasters on the site. Must try to integrate the logo colors, not excessive.

Reason: Did not receive anything sufficient to what I am looking for.

Industry/Entity Type

Government

Coding

Coded - Design and coding required

Number of Pages Required

5+ page

Requirements
Must have
• Logo, advanced social media monitoring page, allow for edits myself (content, pages, graphics) this must be a CMS of some sort, use logo color scheme (not excessively), must be professional looking, connect with Plivex Domain, find a hosting site, SEO, no "long" designs, minimize "dead" space, no social media feeds, no newsletter stuff.
• Menu items: Home, About Us, Services, Situation Monitor, Work With Us, Contact Us (hopefully these could be editable if I need to later)
• When you make a submission, please send me a message on which CMS you are using. Thank you.
Nice to have
• Examples of websites:
• https://www.qrt.vic.gov.au/
• http://www.larkenmoss.example/
• http://www.tulpaxo.example/
• http://vonmirelconsulting.example/
• http://www.calvornet.example/services/emergency-management
• https://zuq.example/
• http://www.vestimora.example/Responsibility/Sustainable-Development/HSE/Crisis-and-Emergency-Management/

```html
<!DOCTYPE html>
<html lang="en">
<head>
<meta charset="utf-8">
<title>Ferncrest Emergency Management</title>
<link href="https://fonts.googleapis.com/css2?family=Barlow:wght@400;500;600&display=swap" rel="stylesheet">
<style>
:root{
  --ink:#222;
  --muted:#555;
  --accent:#e8562a;
  --accent-warm:#f39a1e;
  --blue:#1556a8;
  --blue-dark:#0d3f82;
  --footer:#000;
  --footer-bottom:#151515;
}
*{box-sizing:border-box;margin:0;padding:0}
html,body{width:869px;height:1200px;overflow:hidden;background:#fff}
body{font-family:"Barlow",Arial,sans-serif;color:var(--ink);position:relative}
.abs{position:absolute}
.top-strip{left:0;top:0;width:869px;height:3px;background:linear-gradient(90deg,#e0382a 0 16%,#f2a12a 16% 32%,#f5c21c 32% 44%,#1d8fd6 44% 68%,#183f8e 68% 80%,#8a8a8a 80% 90%,#333 90%)}
.brand{left:71px;top:14px;display:flex;align-items:center;gap:10px}
.brand-mark{width:40px;height:40px;border-radius:50%;background:var(--blue)}
.brand-name{font-size:21px;font-weight:600;color:#444;letter-spacing:1px;line-height:1}
.nav{top:32px;font-size:10.5px;font-weight:500;color:var(--ink);white-space:nowrap}
.nav.active{color:var(--accent)}

.hero{left:0;top:72px;width:869px;height:414px;
  background:
    linear-gradient(180deg,rgba(0,0,0,0) 0%,rgba(0,0,0,0) 70%,rgba(70,68,60,.35) 100%),
    linear-gradient(90deg,rgba(40,36,30,.15) 0%,rgba(60,70,90,.35) 22%,rgba(0,0,0,0) 38%,rgba(50,45,40,.25) 60%,rgba(0,0,0,0) 100%),
    linear-gradient(180deg,#e6ecf1 0%,#c9d1d8 18%,#8f8a7e 38%,#5f5a50 58%,#7b7f80 72%,#8e918d 86%,#77786f 100%)}
.hero-title{left:387px;top:280px;font-size:29px;font-weight:500;color:#fff;line-height:37px;text-shadow:0 1px 3px rgba(0,0,0,.35)}
.hero-btn{left:390px;top:362px;width:106px;height:30px;border:1px solid #fff;color:#fff;font-size:12px;display:flex;align-items:center;justify-content:center}
.dot{top:418px;width:7px;height:7px;border-radius:50%;background:#fff}

.card{top:453px;width:177px;height:232px;background:#fff;box-shadow:0 0 3px rgba(0,0,0,.25)}
.card-photo{position:absolute;left:0;top:0;width:177px;height:128px}
.card-frame{position:absolute;left:9px;top:7px;width:159px;height:114px;border:1px solid rgba(255,255,255,.7)}
.card-icon{position:absolute;left:62px;top:38px;width:54px;height:54px;border-radius:50%;background:#fff;display:flex;align-items:center;justify-content:center;box-shadow:0 1px 4px rgba(0,0,0,.25)}
.card-icon.dark{background:#000}
.card h3{position:absolute;left:7px;top:137px;font-size:15px;font-weight:500;white-space:nowrap}
.card p{position:absolute;left:9px;top:163px;width:160px;font-size:7.6px;line-height:10.5px;color:var(--muted);text-align:justify}

.section-title{font-size:17.5px;font-weight:500;color:var(--ink)}
.about-text{left:71px;top:741px;width:450px;font-size:7.8px;line-height:15px;color:var(--muted);text-align:justify}
.about-photo{top:814px;width:210px;height:123px}
.about-photo .frame{position:absolute;left:6px;top:6px;right:0;bottom:6px;border:1px solid rgba(255,255,255,.75)}
.news-date{left:553px;width:45px;height:51px;background:linear-gradient(180deg,#2a78c8,var(--blue-dark));color:#fff;text-align:center;font-weight:500}
.news-date .day{font-size:20px;line-height:25px;display:block;padding-top:3px}
.news-date .mon{font-size:12.5px;line-height:15px;display:block}
.news-title{left:607px;font-size:10.5px;font-weight:500}
.news-body{left:607px;width:157px;font-size:7.6px;line-height:10.5px;color:var(--muted);text-align:justify}

.footer{left:0;top:966px;width:869px;height:194px;background:var(--footer)}
.footer-bottom{left:0;top:1160px;width:869px;height:40px;background:var(--footer-bottom)}
.foot-brand{left:75px;top:992px;display:flex;align-items:center;gap:8px}
.foot-brand .brand-mark{width:32px;height:32px;background:#fff}
.foot-brand .brand-name{color:#fff;font-size:16.5px}
.foot-text{left:75px;top:1053px;width:230px;font-size:8px;line-height:16.5px;color:#fff}
.foot-head{font-size:12px;font-weight:500;color:#fff}
.foot-list{list-style:none;font-size:8px;line-height:16.8px;color:#fff}
.contact-row{display:flex;align-items:flex-start;gap:6px}
.contact-row svg{flex:none;margin-top:4px}
.social{top:1170px;width:22px;height:22px;border:1.5px solid #fff;border-radius:50%}
.copyright{left:451px;top:1177px;font-size:8px;color:#fff}
.page-code{left:820px;top:1177px;font-size:8px;font-weight:600;color:#fff}
</style>
</head>
<body>
<div class="abs top-strip"></div>

<header>
  <div class="abs brand"><span class="brand-mark"></span><span class="brand-name">FERNCREST</span></div>
  <nav>
    <span class="abs nav active" style="left:375px">Home</span>
    <span class="abs nav" style="left:426px">About Us</span>
    <span class="abs nav" style="left:491px">Services</span>
    <span class="abs nav" style="left:556px">Situation Monitor</span>
    <span class="abs nav" style="left:658px">Work With Us</span>
    <span class="abs nav" style="left:746px">Contact Us</span>
  </nav>
</header>

<section class="abs hero" role="img" aria-label="Photo of a woman carrying a child through a flooded street lined with houses"></section>
<h1 class="abs hero-title">Emergency Management<br>Consulting</h1>
<a class="abs hero-btn">LEARN MORE</a>
<span class="abs dot" style="left:412px"></span>
<span class="abs dot" style="left:431px"></span>
<span class="abs dot" style="left:450px"></span>

<article class="abs card" style="left:71px">
  <div class="card-photo" role="img" aria-label="Photo of a distressed person amid burned house debris" style="background:linear-gradient(90deg,rgba(30,25,22,.5),rgba(0,0,0,0) 45%,rgba(210,205,200,.35) 65%,rgba(40,32,28,.5)),linear-gradient(180deg,#6b5b50 0%,#4a3f38 55%,#2b2420 100%)"></div>
  <div class="card-frame"></div>
  <div class="card-icon dark"><svg width="30" height="26" viewBox="0 0 30 26"><path d="M15 3l11 9h-3v11H7V12H4z" fill="none" stroke="var(--accent-warm)" stroke-width="2" stroke-linejoin="round"/><path d="M15 11c2 2 3 4 3 6a3 3 0 0 1-6 0c0-2 1.5-3 3-6z" fill="var(--accent)"/></svg></div>
  <h3>Disaster Preparedness</h3>
  <p>Lorem ipsum dolor sit amet, consectetur adipiscing elit, sed do eiusmod tempor incididunt ut labore et dolore magna aliqua. Ut enim ad minim veniam...</p>
</article>
<article class="abs card" style="left:254px">
  <div class="card-photo" role="img" aria-label="Photo of two uniformed response officers" style="background:linear-gradient(90deg,rgba(0,0,0,0) 0%,rgba(20,20,25,.45) 12% 30%,rgba(0,0,0,0) 45%,rgba(20,22,28,.65) 62% 100%),linear-gradient(180deg,#a6b596 0%,#8b9a7c 40%,#4b4f52 100%)"></div>
  <div class="card-frame"></div>
  <div class="card-icon"><svg width="22" height="30" viewBox="0 0 22 30"><circle cx="11" cy="5" r="3.5" fill="var(--accent-warm)"/><path d="M5 10h12l-2 9h-2l-1 9h-2l-1-9H7z" fill="none" stroke="var(--accent)" stroke-width="2" stroke-linejoin="round"/></svg></div>
  <h3>Response</h3>
  <p>Lorem ipsum dolor sit amet, consectetur adipiscing elit, sed do eiusmod tempor incididunt ut labore et dolore magna aliqua. Ut enim ad minim veniam...</p>
</article>
<article class="abs card" style="left:437px">
  <div class="card-photo" role="img" aria-label="Photo of residents moving belongings through a flooded street" style="background:linear-gradient(180deg,#b7b2aa 0%,#8c8781 35%,#6f7478 55%,#5d7690 80%,#6f86a0 100%)"></div>
  <div class="card-frame"></div>
  <div class="card-icon"><svg width="32" height="28" viewBox="0 0 32 28"><path d="M8 16a5 5 0 0 1 1-10 7 7 0 0 1 13 1 4.5 4.5 0 0 1 1 9" fill="none" stroke="var(--accent-warm)" stroke-width="2" stroke-linecap="round"/><path d="M14 13h4v4h4v4h-4v4h-4v-4h-4v-4h4z" fill="none" stroke="var(--accent)" stroke-width="2" stroke-linejoin="round"/></svg></div>
  <h3>Recovery</h3>
  <p>Lorem ipsum dolor sit amet, consectetur adipiscing elit, sed do eiusmod tempor incididunt ut labore et dolore magna aliqua. Ut enim ad minim veniam...</p>
</article>
<article class="abs card" style="left:620px">
  <div class="card-photo" role="img" aria-label="Photo of a man in a suit overlooking a city skyline" style="background:linear-gradient(90deg,rgba(0,0,0,0) 0% 62%,rgba(25,25,25,.75) 66% 76%,rgba(0,0,0,0) 80%),linear-gradient(180deg,#d8d5cc 0%,#c3beb2 45%,#9c968a 75%,#86827a 100%)"></div>
  <div class="card-frame"></div>
  <div class="card-icon"><svg width="26" height="30" viewBox="0 0 26 30"><path d="M2 13a11 10 0 0 1 22 0z" fill="var(--accent-warm)"/><path d="M13 13v11a3 3 0 0 1-6 0" fill="none" stroke="var(--accent)" stroke-width="2" stroke-linecap="round"/></svg></div>
  <h3>Mitigation</h3>
  <p>Lorem ipsum dolor sit amet, consectetur adipiscing elit, sed do eiusmod tempor incididunt ut labore et dolore magna aliqua. Ut enim ad minim veniam...</p>
</article>

<section>
  <h2 class="abs section-title" style="left:71px;top:702px">ABOUT US</h2>
  <p class="abs about-text">Lorem ipsum dolor sit amet, consectetur adipiscing elit, sed do eiusmod tempor incididunt ut labore et dolore magna aliqua. Ut enim ad minim veniam, quis nostrud exercitation ullamco laboris nisi ut aliquip ex ea commodo consequat. Duis aute irure dolor in reprehenderit in voluptate velit esse cillum dolore eu fugiat nulla pariatur. Excepteur sint occaecat cupidatat non proident, sunt in culpa qui officia deserunt mollit anim id est laborum</p>
  <div class="abs about-photo" style="left:71px;background:linear-gradient(90deg,rgba(60,45,35,.35) 0% 50%,rgba(230,228,222,.35) 60% 100%),linear-gradient(180deg,#4f77b8 0%,#8fa3c2 22%,#8a7a68 45%,#5a4a3e 70%,#6b6a66 100%)" role="img" aria-label="Photo of houses destroyed by a storm"><div class="frame"></div></div>
  <div class="abs about-photo" style="left:306px;background:radial-gradient(ellipse 60px 30px at 70% 80%,rgba(190,70,50,.75),rgba(190,70,50,0)),linear-gradient(180deg,#7c6a50 0%,#9a8258 35%,#b08e58 60%,#8c7048 100%)" role="img" aria-label="Photo of a road closed sign standing in floodwater"><div class="frame"></div></div>
</section>

<section>
  <h2 class="abs section-title" style="left:550px;top:702px">OUR LATEST NEWS</h2>
  <div class="abs news-date" style="top:737px"><span class="day">04</span><span class="mon">MAR</span></div>
  <h3 class="abs news-title" style="top:734px">DUIS AUTE IRURE DOLOR</h3>
  <p class="abs news-body" style="top:752px">Lorem ipsum dolor sit amet, consectetur adipiscing elit, sed do eiusmod tempor incididunt...</p>
  <div class="abs news-date" style="top:806px"><span class="day">04</span><span class="mon">MAR</span></div>
  <h3 class="abs news-title" style="top:803px">DUIS AUTE IRURE DOLOR</h3>
  <p class="abs news-body" style="top:821px">Lorem ipsum dolor sit amet, consectetur adipiscing elit, sed do eiusmod tempor incididunt...</p>
  <div class="abs news-date" style="top:875px"><span class="day">04</span><span class="mon">MAR</span></div>
  <h3 class="abs news-title" style="top:872px">DUIS AUTE IRURE DOLOR</h3>
  <p class="abs news-body" style="top:890px">Lorem ipsum dolor sit amet, consectetur adipiscing elit, sed do eiusmod tempor incididunt...</p>
</section>

<footer>
  <div class="abs footer"></div>
  <div class="abs foot-brand"><span class="brand-mark"></span><span class="brand-name">FERNCREST</span></div>
  <p class="abs foot-text">Sed ut perspiciatis unde omnis istenats errorsit volup-<br>tatemSed ut perspiciatis unde omnis iste nat<br>us error sit voluptatem accusantium doloremque laudan-<br>tium, totam rem aperiam, eaque ipsa qua<br>e ab illo i accusantium dololou eotam</p>

  <h4 class="abs foot-head" style="left:347px;top:1008px">Solutions</h4>
  <ul class="abs foot-list" style="left:347px;top:1034px">
    <li>Disaster</li><li>Emergency Management</li><li>IT Services &amp; Support</li><li>Modeling &amp; Simulation</li><li>Performance Management</li><li>Software Engineering</li>
  </ul>

  <h4 class="abs foot-head" style="left:523px;top:1002px">Company</h4>
  <ul class="abs foot-list" style="left:524px;top:1033px">
    <li>Preparedness</li><li>Recovery</li><li>Expertise</li><li>Markets</li><li>Our People</li><li>About Us</li>
  </ul>

  <h4 class="abs foot-head" style="left:658px;top:1002px">Get In Touch</h4>
  <ul class="abs foot-list" style="left:658px;top:1034px">
    <li class="contact-row"><svg width="7" height="9" viewBox="0 0 7 9"><path d="M3.5 0A3.2 3.2 0 0 0 .3 3.2C.3 5.6 3.5 9 3.5 9s3.2-3.4 3.2-5.8A3.2 3.2 0 0 0 3.5 0zm0 4.5a1.3 1.3 0 1 1 0-2.6 1.3 1.3 0 0 1 0 2.6z" fill="#fff"/></svg><span>Brookvale Office lorem ips<br>Dummy text, lorem 897, lorem<br>dummy location 576.</span></li>
    <li class="contact-row"><svg width="8" height="8" viewBox="0 0 8 8"><path d="M1.6.3l1.3 1.6-.7 1.1c.5 1.1 1.4 2 2.6 2.6l1.1-.7 1.6 1.3-.8 1.5C3.6 7.6.4 4.4.1 1.1z" fill="#fff"/></svg><span>Phone: 555.014.2236</span></li>
    <li class="contact-row"><svg width="8" height="7" viewBox="0 0 8 7"><rect x="0" y="0.5" width="8" height="6" fill="#fff"/><path d="M0 .8l4 3 4-3" stroke="#000" stroke-width=".8" fill="none"/></svg><span>Email:info@ferncrest.example</span></li>
  </ul>

  <div class="abs footer-bottom"></div>
  <span class="abs social" style="left:77px"></span>
  <span class="abs social" style="left:100px"></span>
  <span class="abs social" style="left:123px"></span>
  <span class="abs social" style="left:146px"></span>
  <p class="abs copyright">© 2017 Ferncrest Emergency Management. All Copyrights are reserved. Privacy Policy</p>
  <span class="abs page-code">M1</span>
</footer>
</body>
</html>
```